business card design for a plumbing contractor

i need a double business card for a plumbing business, our initial service is residential Sewer Drain Cleaning.

Target Market(s)

other plumbing Business

Industry/Entity Type

Plumbing

Contact Information for Business Card

www.PipeworksTopMark.example- 5307218394-

Font styles to use
Serif

Colors
ec1f27
0455a3

```html
<!DOCTYPE html>
<html lang="en">
<head>
<meta charset="utf-8">
<title>Pipeworks Top Mark – Business Card</title>
<link rel="stylesheet" href="https://fonts.googleapis.com/css2?family=Arimo:wght@400;700&display=swap">
<style>
  :root {
    --brand-red: #ec1f27;
    --brand-blue: #0455a3;
    --card-blue: #2766a6;
    --logo-grey: #6e6558;
    --ink: #1c1c1c;
    --paper: #f4f4f4;
    --backdrop: #2b2b2b;
  }
  * { box-sizing: border-box; margin: 0; padding: 0; }
  html, body { width: 1200px; height: 997px; overflow: hidden; }
  body {
    background: var(--backdrop);
    font-family: "Arimo", Arial, sans-serif;
    position: relative;
  }
  .card {
    position: absolute;
    left: 250px;
    width: 700px;
    height: 400px;
    border-radius: 26px;
    overflow: hidden;
  }
  .card-front { top: 66px; background: var(--card-blue); }
  .card-back { top: 531px; background: var(--paper); }

  /* front side */
  .brand-plate {
    position: absolute;
    left: 235px; top: 150px;
    width: 230px; height: 100px;
    background: #f1f1ee;
    border-radius: 18px;
    display: flex; align-items: center; justify-content: center;
  }
  .brand-name {
    color: var(--logo-grey);
    font-weight: 700;
    font-size: 26px;
    line-height: 1.05;
    text-align: center;
  }
  .service {
    position: absolute;
    color: #e8eef6;
    font-size: 15px;
    letter-spacing: .3px;
  }
  .service-maintenance { left: 48px; top: 300px; }
  .service-trenchless { left: 235px; top: 262px; }
  .service-sewer { left: 480px; top: 120px; }

  /* back side */
  .card-back svg.bands { position: absolute; inset: 0; }
  .brand-lockup {
    position: absolute;
    left: 150px; top: 95px;
    display: flex; align-items: center; gap: 16px;
  }
  .brand-lockup .brand-name { font-size: 46px; text-align: left; }
  .brand-mark {
    width: 30px; height: 30px;
    background: var(--brand-red);
  }
  .person {
    position: absolute;
    right: 46px; top: 200px;
    text-align: right;
  }
  .person-name { color: var(--brand-red); font-weight: 700; font-size: 17px; letter-spacing: .5px; }
  .person-role { color: var(--brand-blue); font-size: 15px; }
  .contact-list {
    position: absolute;
    left: 62px; top: 258px;
    list-style: none;
    color: var(--ink);
    font-size: 16px;
    line-height: 27px;
  }
</style>
</head>
<body>

<section class="card card-front" aria-label="Card front">
  <div class="brand-plate"><p class="brand-name">Pipeworks<br>Top Mark</p></div>
  <p class="service service-maintenance">Maintenance</p>
  <p class="service service-trenchless">Trenchless Pipe Installs.</p>
  <p class="service service-sewer">Sewer Drain Cleaning</p>
</section>

<section class="card card-back" aria-label="Card back">
  <svg class="bands" width="700" height="400" viewBox="0 0 700 400" aria-hidden="true">
    <path class="band-red" d="M0 382 C200 378 420 364 575 338 L575 400 L0 400 Z" fill="var(--brand-red)"/>
    <path class="band-blue" d="M566 400 L572 340 Q590 302 645 298 L700 298 L700 400 Z" fill="var(--brand-blue)"/>
    <rect x="-12" y="248" width="50" height="110" rx="12" fill="var(--brand-blue)"/>
    <rect x="690" y="160" width="20" height="40" rx="6" fill="var(--brand-blue)"/>
    <rect x="14" y="262" width="11" height="18" rx="2" fill="none" stroke="#fff" stroke-width="2"/>
    <rect x="12" y="296" width="15" height="11" rx="1" fill="#fff"/>
    <path d="M12 297 L19.5 303 L27 297" fill="none" stroke="var(--brand-blue)" stroke-width="1.5"/>
    <path d="M19.5 338 C14 331 13 328 13 325 A6.5 6.5 0 0 1 26 325 C26 328 25 331 19.5 338 Z" fill="#fff"/>
    <circle cx="19.5" cy="325" r="2.2" fill="var(--brand-blue)"/>
  </svg>

  <div class="brand-lockup">
    <p class="brand-name">Pipeworks<br>Top Mark</p>
    <span class="brand-mark" aria-hidden="true"></span>
  </div>

  <div class="person">
    <p class="person-name">MATEO CARRILLO</p>
    <p class="person-role">Director</p>
  </div>

  <ul class="contact-list">
    <li>5307218394</li>
    <li>Dispatcher@PipeworksTopMark.example</li>
    <li>www.PipeworksTopMark.example</li>
  </ul>
</section>

</body>
</html>
```